Velmarotix - world unique technology for better life - please let them know who am i at first sight

We need a new business card for company which is a provider of unique crystal based technology suitable for all living being. For more information and final design you can use our brochure (our colours are black and blue from brochure).
We use Verdana font

Industry/Entity Type

Business

Contact Information for Business Card

regular dimension

Font styles to use
Other font styles liked:
• Verdana

Requirements
Must have
• Logo
• name
• function/position
• phone
• mobile
• e-mail
• adress
Nice to have
• inovative design (technology directed)

```html
<!DOCTYPE html>
<html lang="en">
<head>
<meta charset="utf-8">
<title>Velmarotix Technologies – Business Card</title>
<link rel="stylesheet" href="https://fonts.googleapis.com/css2?family=Questrial&display=swap">
<style>
  :root {
    --brand-blue: #0aa3e2;
    --ink: #2b2b2b;
    --ink-soft: #4a4a4a;
    --band-grey: #a7a9ab;
    --card-white: #fbfbfb;
    --card-shade: #e4e5e6;
    --page-bg: #d9dadb;
  }
  * { margin: 0; padding: 0; box-sizing: border-box; }
  html, body {
    width: 1200px; height: 900px; overflow: hidden;
    background: var(--page-bg);
    font-family: "Questrial", Verdana, sans-serif;
  }
  .canvas { position: relative; width: 1200px; height: 900px; }
  .card {
    position: absolute; left: 320px;
    width: 560px; height: 320px;
    border-radius: 30px; overflow: hidden;
    box-shadow: 0 6px 20px rgba(0,0,0,.18);
  }
  .card-front {
    top: 110px;
    background: linear-gradient(160deg, var(--card-white) 0%, var(--card-shade) 100%);
  }
  .card-back { top: 470px; background: var(--brand-blue); }

  .card-waves { position: absolute; inset: 0; }

  .brand { position: absolute; display: flex; align-items: center; gap: 16px; color: var(--brand-blue); }
  .brand-mark { width: 70px; height: 70px; border-radius: 50%; background: var(--brand-blue); flex: none; }
  .brand-name { font-size: 40px; letter-spacing: 1px; line-height: 1; text-transform: uppercase; }
  .brand-line { display: block; font-size: 13px; letter-spacing: 9px; margin-top: 8px; padding-left: 4px; }
  .card-front .brand { left: 112px; top: 48px; }

  .card-back .brand { left: 50%; top: 50%; transform: translate(-50%, -50%); color: #fff; }
  .card-back .brand-mark { background: #fff; }

  .holder {
    position: absolute; right: 300px; top: 140px;
    text-align: right; color: var(--ink);
    font-variant: small-caps; letter-spacing: 1.5px;
  }
  .holder-name { font-size: 17px; font-weight: 700; letter-spacing: 2.5px; }
  .holder-role { font-size: 14px; margin-top: 3px; color: var(--ink-soft); }
  .holder-address { font-size: 14px; margin-top: 16px; line-height: 1.3; color: var(--ink-soft); }

  .divider { position: absolute; left: 272px; top: 142px; width: 1px; height: 98px; background: #8d8f91; }

  .contacts {
    position: absolute; left: 284px; top: 141px; list-style: none;
    color: var(--ink); font-size: 14px; letter-spacing: 1.5px; font-variant: small-caps;
  }
  .contacts li { display: flex; align-items: center; gap: 7px; height: 19.5px; }
  .contacts svg { width: 12px; height: 12px; flex: none; }
</style>
</head>
<body>
<main class="canvas">

  <section class="card card-front" aria-label="Business card front">
    <svg class="card-waves" viewBox="0 0 560 320" aria-hidden="true">
      <path d="M0 190 C90 250 260 262 560 258 L560 270 C300 276 130 262 0 232 Z" fill="var(--band-grey)"/>
      <path d="M0 244 C150 268 320 285 560 270 L560 320 L0 320 Z" fill="var(--brand-blue)"/>
    </svg>

    <div class="brand">
      <span class="brand-mark"></span>
      <div class="brand-name">Velmarotix<span class="brand-line">Technologies</span></div>
    </div>

    <div class="holder">
      <p class="holder-name">Daniel Harrow</p>
      <p class="holder-role">Owner / C.E.O</p>
      <p class="holder-address">Suite # 418, Orin Bldg,<br>NY 10427</p>
    </div>

    <span class="divider"></span>

    <ul class="contacts">
      <li><svg viewBox="0 0 12 12"><circle cx="6" cy="6" r="6" fill="var(--ink)"/><path d="M3.5 3 L5 3 L5.5 4.5 L4.8 5.2 Q5.6 6.6 6.8 7.2 L7.5 6.5 L9 7 L9 8.5 Q5 9 3 4.5 Z" fill="#fff"/></svg>214-803-5561</li>
      <li><svg viewBox="0 0 12 12"><circle cx="6" cy="6" r="6" fill="var(--ink)"/><rect x="4" y="2.5" width="4" height="7" rx="0.8" fill="#fff"/></svg>917-362-4480</li>
      <li><svg viewBox="0 0 12 12"><circle cx="6" cy="6" r="6" fill="var(--ink)"/><rect x="3" y="5" width="6" height="4" fill="#fff"/><rect x="4" y="2.5" width="4" height="2.5" fill="#fff"/></svg>312-570-9914</li>
      <li><svg viewBox="0 0 12 12"><circle cx="6" cy="6" r="6" fill="var(--ink)"/><rect x="2.8" y="3.8" width="6.4" height="4.4" fill="#fff"/><path d="M2.8 3.8 L6 6.4 L9.2 3.8" stroke="var(--ink)" stroke-width="0.8" fill="none"/></svg>info@velmarotix.com</li>
      <li><svg viewBox="0 0 12 12"><circle cx="6" cy="6" r="6" fill="var(--ink)"/><circle cx="6" cy="6" r="3.6" fill="none" stroke="#fff" stroke-width="0.9"/><path d="M2.4 6 H9.6 M6 2.4 V9.6" stroke="#fff" stroke-width="0.8"/></svg>www.velmarotix.com</li>
    </ul>
  </section>

  <section class="card card-back" aria-label="Business card back">
    <div class="brand">
      <span class="brand-mark"></span>
      <div class="brand-name">Velmarotix<span class="brand-line">Technologies</span></div>
    </div>
  </section>

</main>
</body>
</html>
```